Beacon Advisory Website

I currently have a website www.beaconadvisoryinc.com. We are a IT Consulting Company. Our website will pretty much tell out our services. I am looking to enhance my website and make it look more professional. Looking for very classy and Contemporary look and design for my website.

It Company

```html
<!DOCTYPE html>
<html lang="en">
<head>
<meta charset="utf-8">
<title>Beacon Advisory</title>
<link href="https://fonts.googleapis.com/css2?family=Ubuntu:wght@400;500;700&family=Lato:ital,wght@0,400;0,700;1,400&display=swap" rel="stylesheet">
<style>
:root{
  --blue:#1a5aa5;
  --blue-dark:#134a8c;
  --blue-bright:#1d86c9;
  --ink:#333;
  --muted:#555;
  --grey-bg:#ececec;
  --footer:#2b2b2b;
  --line:#c9c9c9;
}
*{margin:0;padding:0;box-sizing:border-box}
html,body{width:709px;height:1200px;overflow:hidden;background:#fff}
body{position:relative;font-family:'Lato',sans-serif;color:var(--ink)}
.abs{position:absolute}
a{color:inherit;text-decoration:none}

/* header */
.header{left:0;top:0;width:709px;height:56px;background:#fff;border-top:2px solid var(--blue-bright)}
.brand{left:32px;top:12px;display:flex;align-items:center;gap:6px;font-family:'Ubuntu',sans-serif;font-weight:700;font-size:17px;color:var(--blue)}
.brand-mark{width:30px;height:30px;border-radius:50%;background:var(--blue)}
.social-pill{left:520px;top:0;width:144px;height:24px;background:var(--blue-bright);border-radius:0 0 20px 20px;display:flex;justify-content:center;align-items:center;gap:7px}
.social-pill span{width:16px;height:16px;border-radius:50%;background:#fff}
.contact-line{top:35px;font-size:9px;color:var(--ink);display:flex;align-items:center;gap:5px}
.nav{left:0;top:56px;width:709px;height:26px;background:var(--blue);display:flex;align-items:center;padding-left:31px}
.nav a{font-family:'Ubuntu',sans-serif;font-weight:500;font-size:9.5px;color:#fff;height:26px;line-height:26px;text-align:center;border-right:1px solid rgba(255,255,255,.15)}
.nav a.active{background:var(--blue-bright)}

/* hero */
.hero{left:0;top:82px;width:709px;height:282px;background:linear-gradient(180deg,#9cc8ea 0%,#d9e8f2 50%,#5a6470 78%,#1e2226 100%)}
.hero-figure{right:0;top:50px;width:290px;height:232px;background:linear-gradient(160deg,#2a2a2a,#050505);clip-path:polygon(55% 0,75% 5%,100% 10%,100% 100%,0 100%,10% 75%,30% 40%)}
.hero-title{left:32px;top:96px;font-family:'Ubuntu',sans-serif;font-weight:500;font-size:19.5px;line-height:29px;color:var(--blue)}
.hero-arrow{top:133px;width:17px;height:17px;background:#3a3f45;display:flex;align-items:center;justify-content:center}

/* feature tiles */
.tile{top:386px;width:197px;height:55px;background:var(--blue);display:flex;align-items:center;padding-left:9px;gap:10px;font-family:'Ubuntu',sans-serif;font-weight:500;font-size:13.5px;color:#fff}
.tile-icon{width:38px;height:38px;border-radius:50%;background:var(--blue-bright);display:flex;align-items:center;justify-content:center}

/* welcome */
.welcome{left:0;top:466px;width:709px;height:174px;background:var(--grey-bg)}
.welcome-title{left:32px;top:17px;font-family:'Ubuntu',sans-serif;font-weight:500;font-size:16.5px;color:#444;display:flex;align-items:center;gap:8px}
.welcome-title b{color:var(--blue);font-weight:500}
.title-dot{width:16px;height:16px;border-radius:50%;background:var(--blue)}
.rule{height:2px;background:var(--blue-bright)}
.welcome-text{left:32px;top:51px;width:420px;font-size:9.4px;line-height:13.7px;color:var(--ink)}
.btn{background:var(--blue);color:#fff;font-size:7.5px;font-weight:700;padding:4px 7px}
.video{left:483px;top:20px;width:195px;height:130px;background:linear-gradient(135deg,#cfdde8,#8fa8bd 60%,#5c7185);box-shadow:0 2px 5px rgba(0,0,0,.35)}
.video-bar{left:0;bottom:0;width:195px;height:18px;background:#1b1b1b;display:flex;align-items:center;padding:0 8px;gap:8px}
.play-btn{left:85px;top:48px;width:25px;height:18px;border-radius:4px;background:#111;display:flex;align-items:center;justify-content:center}

/* services */
.section-title{font-family:'Ubuntu',sans-serif;font-weight:500;font-size:16px;color:#444;text-align:center;width:709px;left:0}
.section-title b{color:var(--blue);font-weight:500}
.service{width:120px;text-align:center}
.service-icon{width:50px;height:50px;border-radius:50%;background:var(--blue);margin:0 auto;display:flex;align-items:center;justify-content:center}
.service h3{font-family:'Ubuntu',sans-serif;font-weight:500;font-size:11.5px;line-height:14px;color:var(--blue);margin-top:7px}
.service p{font-size:8px;line-height:10.5px;margin-top:5px;color:#222}
.service a{display:block;font-size:8px;font-weight:700;color:var(--blue);margin-top:7px}

/* contact */
.contact-band{left:0;top:856px;width:709px;height:194px;background:var(--grey-bg)}
.band-title{top:20px;font-family:'Ubuntu',sans-serif;font-weight:500;font-size:13.5px;color:#444;display:flex;align-items:center;gap:6px}
.band-title b{color:var(--blue);font-weight:500}
.band-line{top:38px;height:1px;background:var(--line)}
.field{background:#fff;border:1px solid #ddd;height:16px;font-size:6.5px;color:#333;padding:4px 6px}
.submit{left:287px;top:162px;width:48px;height:16px;background:var(--blue-bright);color:#fff;font-size:7.5px;font-weight:700;text-align:center;line-height:16px}
.quote{left:371px;top:53px;width:307px;height:88px;background:#fff;border-radius:4px;padding:9px 12px 0 14px;font-style:italic;font-size:7.6px;line-height:13px;color:#333}
.avatar{left:386px;top:132px;width:46px;height:46px;border-radius:50%;background:linear-gradient(135deg,#c9a27c,#7a5a3f);border:3px solid #fff;box-shadow:0 1px 3px rgba(0,0,0,.3)}

/* footer */
.footer{left:0;top:1050px;width:709px;height:128px;background:var(--footer);color:#ddd}
.footer h4{position:absolute;top:16px;font-family:'Ubuntu',sans-serif;font-weight:500;font-size:10px;color:#fff}
.footer .fline{position:absolute;top:31px;height:1px;background:#555}
.quick{left:32px;top:43px;font-size:7.5px;line-height:12.4px}
.map{left:396px;top:36px;width:131px;height:67px;background:linear-gradient(135deg,#dfe7d2,#a9c4de 55%,#e6d7b0)}
.follow div{display:flex;align-items:center;gap:8px;font-size:8px;height:18.6px}
.follow span{width:13px;height:13px;background:#fff;border-radius:2px}
.copyright{left:0;top:1178px;width:709px;height:22px;background:var(--blue);color:#fff;font-size:8px;text-align:center;line-height:22px}
</style>
</head>
<body>

<header class="abs header">
  <div class="abs brand"><span class="brand-mark"></span>Beacon Advisory</div>
  <div class="abs social-pill"><span></span><span></span><span></span><span></span></div>
  <div class="abs contact-line" style="left:454px">
    <svg width="9" height="9" viewBox="0 0 10 10"><path d="M2 0l2 2-1 2c1 1 2 2 3 3l2-1 2 2-2 2C4 10 0 6 0 2z" fill="var(--blue)"/></svg>555-010-2468
  </div>
  <div class="abs contact-line" style="left:538px">
    <svg width="10" height="7" viewBox="0 0 10 7"><rect width="10" height="7" fill="var(--blue)"/><path d="M0 0l5 4 5-4" stroke="#fff" fill="none"/></svg>info@beaconadvisory.com
  </div>
</header>

<nav class="abs nav">
  <a class="active" style="width:52px">HOME</a>
  <a style="width:77px">COMPANY</a>
  <a style="width:96px">SERVICES</a>
  <a style="width:104px">SOLUTIONS</a>
  <a style="width:105px">RESOURCES</a>
  <a style="width:89px">CAREER</a>
  <a style="width:113px;border:none">CONTACT US</a>
</nav>

<section class="abs hero">
  <div class="abs hero-figure" role="img" aria-label="Silhouette of one climber helping another up a rocky summit"></div>
  <h1 class="abs hero-title">We Understand The Complexities<br>Management Faces When<br>Staffing A Project</h1>
  <div class="abs hero-arrow" style="left:0"><svg width="6" height="8"><path d="M5 0L1 4l4 4" stroke="#fff" fill="none" stroke-width="1.5"/></svg></div>
  <div class="abs hero-arrow" style="right:0"><svg width="6" height="8"><path d="M1 0l4 4-4 4" stroke="#fff" fill="none" stroke-width="1.5"/></svg></div>
</section>

<div class="abs tile" style="left:41px"><span class="tile-icon"><svg width="18" height="18" viewBox="0 0 18 18"><circle cx="9" cy="5" r="3" fill="#fff"/><path d="M3 16c0-4 3-6 6-6s6 2 6 6z" fill="#fff"/></svg></span>Consulting</div>
<div class="abs tile" style="left:255px"><span class="tile-icon"><svg width="18" height="18" viewBox="0 0 18 18"><circle cx="9" cy="4" r="2.5" fill="#fff"/><circle cx="4" cy="10" r="2" fill="#fff"/><circle cx="14" cy="10" r="2" fill="#fff"/><path d="M1 17c0-3 6-3 6 0zM11 17c0-3 6-3 6 0z" fill="#fff"/></svg></span>Staff Augmentation</div>
<div class="abs tile" style="left:469px"><span class="tile-icon"><svg width="18" height="18" viewBox="0 0 18 18"><path d="M3 3h3v12H3zM12 3h3v12h-3zM1 7h16v3H1z" fill="#fff"/></svg></span>Offshore</div>

<section class="abs welcome">
  <h2 class="abs welcome-title"><span class="title-dot"></span>WELCOME TO <b>BEACON ADVISORY</b></h2>
  <div class="abs rule" style="left:32px;top:40px;width:63px"></div>
  <p class="abs welcome-text">Lorem ipsum dolor sit amet, consectetur adipiscing elit. Nulla in sollicitudin velit, bibendum velit. Cras vel facilisis ipsum, et venenatis risus. In egestas nunc etvb eros auctor sollicitu Etiam ut enim vitae magna volutpat venenatis vitae nonprof diam. Nam nunc velit, tristique a sapien euismod, pulvinar vestibulum dui. Morbi porttitor eu erat imperdiet pretium consequat fcilelis. quis nostrud exerci tation ullamcorper suscipit lobortis nisl ut aliquip ex ea commodo consequat. Duis autem vel eum iriure dolor in hendrerit in vulputate velit esse molestie consequat.</p>
  <a class="abs btn" style="left:32px;top:140px">READ MORE</a>
  <div class="abs video" role="img" aria-label="Video still of a smiling consultant in a bright office">
    <div class="abs play-btn"><svg width="8" height="9"><path d="M0 0l8 4.5L0 9z" fill="#fff"/></svg></div>
    <div class="abs video-bar">
      <svg width="6" height="7"><path d="M0 0l6 3.5L0 7z" fill="#fff"/></svg>
      <svg width="7" height="7"><path d="M0 2h2l3-2v7L2 5H0z" fill="#fff"/></svg>
      <div style="flex:1;height:3px;background:#444;border-radius:2px"><div style="width:45%;height:3px;background:var(--blue-bright);border-radius:2px"></div></div>
      <svg width="7" height="7"><path d="M0 7l3-3M7 0L4 3M4 0h3v3M0 4v3h3" stroke="#fff" fill="none"/></svg>
    </div>
  </div>
</section>

<h2 class="abs section-title" style="top:655px">OUR <b>SERVICES</b></h2>
<div class="abs" style="left:246px;top:684px;width:217px;height:1px;background:var(--line)"></div>
<div class="abs rule" style="left:322px;top:683px;width:64px"></div>

<div class="abs service" style="left:25px;top:707px"><div class="service-icon"><svg width="22" height="22" viewBox="0 0 22 22"><circle cx="8" cy="12" r="5" fill="none" stroke="#fff" stroke-width="3"/><circle cx="16" cy="6" r="3" fill="none" stroke="#fff" stroke-width="2"/></svg></div><h3>Information<br>Technology</h3><p>Lorem ipsum dolor sit amet, consectetuer adipiscing elit,</p><a>Read More »</a></div>
<div class="abs service" style="left:159px;top:707px"><div class="service-icon"><svg width="22" height="22" viewBox="0 0 22 22"><circle cx="11" cy="4" r="2.5" fill="#fff"/><path d="M2 10h18v2H2zM4 12v8M18 12v8M8 12v8M14 12v8" stroke="#fff" stroke-width="2" fill="#fff"/></svg></div><h3>Offshore<br>Business</h3><p>Lorem ipsum dolor sit amet, consectetuer adipiscing elit,</p><a>Read More »</a></div>
<div class="abs service" style="left:294px;top:707px"><div class="service-icon"><svg width="22" height="22" viewBox="0 0 22 22"><rect x="5" y="1" width="10" height="20" rx="2" fill="none" stroke="#fff" stroke-width="2"/><circle cx="14" cy="11" r="4" fill="#fff"/></svg></div><h3>Application<br>Developement</h3><p>Lorem ipsum dolor sit amet, consectetuer adipiscing elit,</p><a>Read More »</a></div>
<div class="abs service" style="left:428px;top:707px"><div class="service-icon"><svg width="22" height="22" viewBox="0 0 22 22"><circle cx="11" cy="11" r="9" fill="none" stroke="#fff" stroke-width="2"/><path d="M6 11a5 3 0 0 1 10 0M16 11a5 3 0 0 1-10 0" stroke="#fff" stroke-width="2" fill="none"/></svg></div><h3>Enterprise<br>Integration</h3><p>Lorem ipsum dolor sit amet, consectetuer adipiscing elit,</p><a>Read More »</a></div>
<div class="abs service" style="left:563px;top:707px"><div class="service-icon"><svg width="22" height="22" viewBox="0 0 22 22"><circle cx="11" cy="11" r="7" fill="none" stroke="#fff" stroke-width="3" stroke-dasharray="3 2"/><path d="M6 17l10-10" stroke="#fff" stroke-width="2"/></svg></div><h3>IT<br>Consulting</h3><p>Lorem ipsum dolor sit amet, consectetuer adipiscing elit,</p><a>Read More »</a></div>

<section class="abs contact-band">
  <h2 class="abs band-title" style="left:32px"><svg width="13" height="10" viewBox="0 0 13 10"><rect width="13" height="10" fill="#222"/><path d="M0 0l6.5 5L13 0" stroke="#fff" fill="none"/></svg>GET IN <b>TOUCH WITH US</b></h2>
  <div class="abs band-line" style="left:32px;width:307px"></div>
  <div class="abs rule" style="left:32px;top:37px;width:63px"></div>
  <p class="abs" style="left:32px;top:51px;font-size:7.5px">Lorem ipsum dolor sit amet consectetuer adipiscing sed dmmy nibh</p>
  <div class="abs field" style="left:31px;top:70px;width:144px">Name</div>
  <div class="abs field" style="left:190px;top:70px;width:145px">Email</div>
  <div class="abs field" style="left:31px;top:92px;width:144px">Phone Number</div>
  <div class="abs field" style="left:190px;top:92px;width:145px">Enquiry Type<svg style="position:absolute;right:6px;top:5px" width="7" height="5"><path d="M0 0l3.5 4L7 0" stroke="#888" fill="none"/></svg></div>
  <div class="abs field" style="left:31px;top:114px;width:304px;height:37px">Your Message</div>
  <div class="abs submit">SUBMIT</div>

  <h2 class="abs band-title" style="left:370px"><svg width="13" height="11" viewBox="0 0 13 11"><path d="M0 0h9v6H3L1 8V6H0z" fill="#222"/><path d="M10 3h3v6h-1v2l-2-2H5V7h5z" fill="#222"/></svg>CLIENT <b>TESTIMONIALS</b></h2>
  <div class="abs band-line" style="left:370px;width:307px"></div>
  <div class="abs rule" style="left:370px;top:37px;width:63px"></div>
  <div class="abs quote"><span style="font-size:20px;color:#ccc;font-family:Georgia,serif;line-height:0">“</span> Lorem ipsum dolor sit amet consetug e sed diay nibh euismodl tincidunt ut laoreet dolore magam er vol wisi enim ad minim veniam quis nostrud exerciorem ipsum dolor sit ametee sed diammmy nibh euismd tincidunt ut laoreet doloregna aliqur volpatl tiidunt ut laoreet dolore magna aliqur volpatl</div>
  <svg class="abs" style="left:598px;top:140px" width="30" height="14"><path d="M0 0h30L5 14z" fill="#fff"/></svg>
  <div class="abs avatar" role="img" aria-label="Client portrait"></div>
  <p class="abs" style="left:467px;top:156px;font-size:8px;font-weight:700;color:var(--blue)">Mr.Ellis Warren</p>
</section>

<footer class="abs footer">
  <h4 style="left:32px">Quick Links</h4><div class="fline" style="left:32px;width:73px"></div>
  <div class="abs quick">› Home<br>› Company<br>› Services<br>› Solutions<br>› Resources<br>› Career<br>› Contact Us</div>

  <h4 style="left:180px">Contact Details</h4><div class="fline" style="left:180px;width:141px"></div>
  <svg class="abs" style="left:180px;top:44px" width="7" height="10"><path d="M3.5 0a3.5 3.5 0 0 1 3.5 3.5C7 6 3.5 10 3.5 10S0 6 0 3.5A3.5 3.5 0 0 1 3.5 0z" fill="#fff"/><circle cx="3.5" cy="3.5" r="1.3" fill="var(--footer)"/></svg>
  <p class="abs" style="left:195px;top:42px;font-size:8px;line-height:11px"><b style="color:#fff">Beacon Advisory INC.</b><br>48 Harbor Lane, Suite 12<br>Westfield, NJ 07090</p>
  <svg class="abs" style="left:180px;top:80px" width="8" height="8" viewBox="0 0 10 10"><path d="M2 0l2 2-1 2c1 1 2 2 3 3l2-1 2 2-2 2C4 10 0 6 0 2z" fill="#fff"/></svg>
  <p class="abs" style="left:195px;top:79px;font-size:8px">555-010-2468</p>
  <svg class="abs" style="left:180px;top:105px" width="9" height="6"><rect width="9" height="6" fill="#fff"/><path d="M0 0l4.5 3.5L9 0" stroke="var(--footer)" fill="none"/></svg>
  <p class="abs" style="left:195px;top:103px;font-size:8px">info@beaconadvisory.com</p>

  <h4 style="left:396px">Location Map</h4><div class="fline" style="left:396px;width:131px"></div>
  <div class="abs map" role="img" aria-label="Street map showing the office location"></div>
  <p class="abs" style="left:397px;top:109px;font-size:8px">View Location ››</p>

  <h4 style="left:602px">Follow Us</h4><div class="fline" style="left:602px;width:73px"></div>
  <div class="abs follow" style="left:602px;top:44px">
    <div><span></span>Circleboard</div>
    <div><span></span>Chirpline</div>
    <div><span></span>Globeplus</div>
    <div><span></span>Workmesh</div>
  </div>
</footer>

<div class="abs copyright">© 2016 Beacon Advisory &nbsp;|&nbsp; All rights reserved</div>

</body>
</html>
```